4th Generation Family Business Needs a New Card Design!

We are a family owned 4th Generation company. We are based in the Sydney, Australia area and we are desperately in need of a more modern and classy card. We are monumental masons who design, supply & erect lasting memorials throughout cemeteries in Sydney. Our customers are normally in a period of grieving. I have attached logo files that will need to be implemented on the card. Company was established 1935. Australian Owned and Operated. Card needs to be designed to PIXO.com specification.

Target Market(s)

Our target market is based upon people that a grieving for family members that have passed away. We also deal with alot of companies that own and operate cemeteries.

Industry/Entity Type

Business

Contact Information for Business Card

Simon Harcourt, Operations Manager, 0417293086, simon@harcourtmemorials.com.au
Lewis Harcourt, Director, 0491630572, lewis@harcourtmemorials.com.au
Phone # 02 9561 3048
Website: www.harcourtmemorials.com.au
Address: Suite 17, 8 Palfrey Lane, West Carlow, Sydney NSW 2156

Font styles to use
Serif
Decorative
Script

Requirements
Must have
• Would like to see the logo nicely implemented with a modern design. Embossed lettering would be a nice additive.

```html
<!DOCTYPE html>
<html lang="en">
<head>
<meta charset="utf-8">
<title>Harcourt Memorials — Business Card</title>
<link href="https://fonts.googleapis.com/css2?family=Cinzel:wght@500&family=Open+Sans:wght@400;600&display=swap" rel="stylesheet">
<style>
  :root {
    --backdrop: #8f8f8f;
    --card-white: #f4f4f2;
    --ink: #1d1b1a;
    --ink-soft: #3a3a3a;
    --gold: #d1ab22;
    --gold-deep: #c49e1c;
    --gold-pattern: #c8a21e;
    --rule: #8a8a8a;
    --paper-text: #ffffff;
  }
  * { box-sizing: border-box; margin: 0; padding: 0; }
  html, body {
    width: 1105px; height: 1200px; overflow: hidden;
    background: var(--backdrop);
    font-family: "Open Sans", Arial, sans-serif;
  }
  .canvas { position: relative; width: 1105px; height: 1200px; }

  .card {
    position: absolute; left: 179px; width: 747px; height: 427px;
    overflow: hidden;
    box-shadow: 0 6px 14px rgba(0,0,0,0.28);
  }

  /* Front */
  .card-front { top: 118px; background: var(--card-white); }
  .brand-name {
    position: absolute; right: 34px; top: 150px; width: 260px;
    text-align: center; font-family: "Cinzel", Georgia, serif; font-weight: 500;
    color: var(--ink); line-height: 1;
  }
  .brand-name .brand-main { display: block; font-size: 40px; letter-spacing: 0.5px; }
  .brand-name .brand-sub { display: block; font-size: 19px; letter-spacing: 1.5px; margin-top: 8px; }

  .person { position: absolute; left: 39px; top: 201px; }
  .person-name { font-size: 23px; font-weight: 600; color: var(--ink); }
  .person-role { font-size: 19px; color: var(--gold); margin-top: 2px; }

  .divider {
    position: absolute; left: 39px; top: 265px; width: 674px;
    height: 1.5px; background: var(--rule);
  }

  .contact-list { position: absolute; left: 39px; top: 278px; list-style: none; }
  .contact-list li {
    display: flex; align-items: center; gap: 10px;
    height: 29px; font-size: 18px; color: var(--ink-soft);
  }
  .contact-list svg { width: 17px; height: 17px; fill: var(--ink); flex: none; }

  .address {
    position: absolute; right: 34px; top: 307px; text-align: right;
    font-size: 18px; line-height: 29px; color: var(--ink-soft);
  }

  .footer-band { position: absolute; left: 0; bottom: 0; width: 747px; height: 40px; }
  .web-front {
    position: absolute; right: 26px; bottom: 8px;
    font-size: 19px; color: var(--paper-text);
  }

  /* Back */
  .card-back { top: 638px; background: var(--gold); }
  .back-texture {
    position: absolute; inset: 0;
    background: linear-gradient(135deg, var(--gold) 0%, var(--gold-pattern) 50%, var(--gold-deep) 100%);
  }
  .back-brand {
    position: absolute; left: 0; right: 0; top: 150px; text-align: center;
    font-family: "Cinzel", Georgia, serif; font-weight: 500; color: var(--ink); line-height: 1;
  }
  .back-brand .brand-main { display: block; font-size: 62px; letter-spacing: 1px; }
  .back-brand .brand-sub { display: block; font-size: 30px; letter-spacing: 2px; margin-top: 10px; }
  .web-back {
    position: absolute; left: 0; right: 0; top: 272px; text-align: center;
    font-size: 20px; font-style: italic; letter-spacing: 3px; color: var(--ink);
  }
</style>
</head>
<body>
<main class="canvas">

  <section class="card card-front" aria-label="Business card front">
    <div class="brand-name">
      <span class="brand-main">HARCOURT</span>
      <span class="brand-sub">MEMORIALS</span>
    </div>

    <div class="person">
      <p class="person-name">Simon Harcourt</p>
      <p class="person-role">Operations Manager</p>
    </div>

    <div class="divider"></div>

    <ul class="contact-list">
      <li>
        <svg viewBox="0 0 24 24" aria-hidden="true"><path d="M6.6 10.8a15.1 15.1 0 0 0 6.6 6.6l2.2-2.2c.3-.3.7-.4 1-.2 1.1.4 2.3.6 3.6.6.6 0 1 .4 1 1V20c0 .6-.4 1-1 1A17 17 0 0 1 3 4c0-.6.4-1 1-1h3.5c.6 0 1 .4 1 1 0 1.3.2 2.5.6 3.6.1.3 0 .7-.2 1z"/></svg>
        02 9561 3048
      </li>
      <li>
        <svg viewBox="0 0 24 24" aria-hidden="true"><path d="M7 1h10a2 2 0 0 1 2 2v18a2 2 0 0 1-2 2H7a2 2 0 0 1-2-2V3a2 2 0 0 1 2-2zm0 3v14h10V4zm5 15.5a1 1 0 1 0 0 2 1 1 0 0 0 0-2z"/></svg>
        0417293086
      </li>
      <li>
        <svg viewBox="0 0 24 24" aria-hidden="true"><path d="M2 5h20v14H2zm2 2v.5l8 5 8-5V7zm0 2.8V17h16V9.8l-8 5z"/></svg>
        simon@harcourtmemorials.com.au
      </li>
    </ul>

    <address class="address" style="font-style: normal;">
      Suite 17, 8 Palfrey Lane<br>
      West Carlow, Sydney NSW 2156
    </address>

    <svg class="footer-band" viewBox="0 0 747 40" aria-hidden="true">
      <rect x="0" y="13" width="410" height="10" fill="var(--gold)"/>
      <polygon points="432,0 747,0 747,40 397,40" fill="var(--ink)"/>
    </svg>
    <p class="web-front">www.harcourtmemorials.com.au</p>
  </section>

  <section class="card card-back" aria-label="Business card back">
    <div class="back-texture" role="img" aria-label="Tone-on-tone gold repeating monogram pattern"></div>
    <div class="back-brand">
      <span class="brand-main">HARCOURT</span>
      <span class="brand-sub">MEMORIALS</span>
    </div>
    <p class="web-back">www.harcourtmemorials.com.au</p>
  </section>

</main>
</body>
</html>
```